Ridgeline Haul Carriers - Website

A clean, not cluttered informative website for our business. We specialize in the transportation of radioactive materials across North America. The site is mostly for information about our company and will not be used to attract business but will be used to attract employee's mainly drivers. Driver's are very hard to find in our area. One of the pages needs to be a job's posting page with an apply now button. Either an application can be filled out there or a resume can be uploaded which ever functionality works better. I would like a website that I can easily edit, ability to change text and photos.

Number of Pages Required

5+ page

Colors

Designer to choose colors to be used in the design.

Requirements
Must have
• Home - About - Services - Jobs - Contact pages
• A way prospective employee's can apply or upload their resume to be emailed to me
• Very clean apperance
Should not have
• I don't want it to be busy

```html
<!DOCTYPE html>
<html lang="en">
<head>
<meta charset="utf-8">
<title>Ridgeline Haul Carriers</title>
<link rel="stylesheet" href="https://fonts.googleapis.com/css2?family=Saira:wght@500;600;700&family=Open+Sans:wght@400;600;700&display=swap">
<style>
:root{
  --red:#e8202a;
  --orange:#f7941d;
  --ink:#1c1c1c;
  --body:#555;
  --grey-band:#f2f2f2;
  --footer:#2b2b2d;
  --white:#fff;
}
*{box-sizing:border-box;margin:0;padding:0}
html,body{width:1200px;height:3333px;overflow:hidden}
body{position:relative;background:var(--white);font-family:"Open Sans",sans-serif;color:var(--body)}
.abs{position:absolute}
.heading{font-family:"Saira",sans-serif;color:var(--ink);font-weight:600}

/* hero */
.hero{left:0;top:0;width:1200px;height:644px;background:linear-gradient(180deg,#3b3b3d 0%,#2a2a2c 55%,#4a4a4c 100%)}
.brand{font-family:"Saira",sans-serif;font-weight:700;color:var(--white);letter-spacing:2px;line-height:1}
.brand-top{left:91px;top:30px;font-size:30px}
.nav{left:629px;top:42px;display:flex;gap:0}
.nav a{position:absolute;color:var(--white);text-decoration:none;font-family:"Saira",sans-serif;font-size:16px;font-weight:500;white-space:nowrap}
.brand-center{left:0;width:1200px;top:256px;text-align:center;font-size:40px}
.see-more{left:0;width:1200px;top:344px;text-align:center;color:var(--orange);font-family:"Saira",sans-serif;font-size:15px;font-weight:600}
.hero-arrow{width:48px;height:48px;border-radius:50%;background:var(--white);top:298px}
.trucks{left:240px;top:400px;width:740px;height:322px;border-radius:6px;background:linear-gradient(90deg,#d9461a 0%,#f07a1c 35%,#f39a1e 65%,#f3b51f 100%)}

/* about */
.about-photo{left:104px;top:838px;width:378px;height:378px;border-radius:50%;background:linear-gradient(180deg,#a9c8e4 0%,#7ea35a 45%,#6c6c6c 75%,#555 100%)}
.about-ring{left:96px;top:826px}
.about-title{left:556px;top:826px;font-size:42px}
.about-text{left:558px;top:904px;width:550px;font-size:14px;line-height:28px;text-align:justify;color:#444}
.btn{display:flex;align-items:center;justify-content:center;color:var(--white);font-family:"Saira",sans-serif;font-weight:600;border-radius:10px}
.btn-red{background:var(--red)}
.btn-orange{background:var(--orange)}
.learn-more{left:558px;top:1104px;width:164px;height:49px;font-size:15px}

/* services */
.services{left:0;top:1278px;width:1200px;height:595px;background:var(--grey-band)}
.services-title{left:0;width:1200px;top:1318px;text-align:center;font-size:42px}
.svc-img{top:1415px;width:294px;height:207px}
.svc-name{top:1640px;font-size:22px}
.svc-text{top:1684px;width:300px;font-size:13.5px;line-height:26px;color:#666}
.svc-more{top:1802px;font-family:"Saira",sans-serif;font-weight:600;font-size:16px;color:var(--red)}
.svc-arrow{width:48px;height:48px;border-radius:50%;background:#555;top:1498px}

/* professional band */
.pro-band{left:0;top:1873px;width:1200px;height:471px;background:linear-gradient(180deg,#0f2440 0%,#1f3c62 55%,#3a4a5c 100%)}
.pro-truck{left:707px;top:1985px;width:415px;height:300px;background:linear-gradient(135deg,#c9ced4 0%,#8d949c 60%,#3f454c 100%);opacity:.9}
.pro-kicker{left:89px;top:1972px;font-family:"Saira",sans-serif;font-size:18px;font-weight:600;color:var(--white)}
.pro-title{left:86px;top:2010px;width:680px;font-family:"Saira",sans-serif;font-size:34px;font-weight:600;color:var(--white);line-height:44px}
.apply{left:87px;top:2118px;width:153px;height:46px;font-size:16px}
.features{left:107px;top:2244px;width:977px;height:340px;background:var(--white);box-shadow:0 4px 14px rgba(0,0,0,.12)}
.feat-icon{width:80px;height:80px;border-radius:50%;background:var(--orange);top:2295px}
.feat-title{top:2400px;width:460px;text-align:center;font-family:"Saira",sans-serif;font-weight:600;font-size:24px;color:var(--red)}
.feat-text{top:2450px;width:460px;text-align:center;font-size:14px;line-height:27px;color:#666}

/* dedicated */
.ded-title{left:0;width:1200px;top:2690px;text-align:center;font-size:36px}
.ded-text{left:200px;width:800px;top:2752px;text-align:center;font-size:14px;line-height:28px;color:#666}
.quote{left:460px;top:2842px;width:307px;height:58px;font-size:19px}

/* footer */
.footer{left:0;top:2989px;width:1200px;height:344px;background:var(--footer)}
.brand-foot{left:91px;top:3092px;font-size:40px}
.social{width:32px;height:32px;border-radius:50%;border:2px solid var(--white);top:3179px}
.foot-head{top:3036px;font-family:"Saira",sans-serif;font-weight:600;font-size:19px;color:var(--white)}
.foot-list{list-style:none;top:3094px}
.foot-list li{font-size:13px;font-weight:600;color:var(--white);height:27px;line-height:27px}
.contact-row{left:858px;font-size:13px;color:var(--white);line-height:26px}
.contact-row b{font-weight:600;font-size:14px;margin-right:6px}
.copy{left:0;width:1200px;top:3284px;text-align:center;font-size:14px;color:var(--white)}
</style>
</head>
<body>

<section class="abs hero" role="img" aria-label="Photo of parked semi trucks and tanker trailers at dusk"></section>
<div class="abs brand brand-top">RIDGELINE HAUL</div>
<nav class="abs nav">
  <a href="#" style="left:0">Home</a>
  <a href="#" style="left:111px">About</a>
  <a href="#" style="left:207px">Services</a>
  <a href="#" style="left:298px">Jobs</a>
  <a href="#" style="left:384px">Contact</a>
  <svg style="position:absolute;left:464px;top:2px" width="18" height="18" viewBox="0 0 18 18"><circle cx="7" cy="7" r="5" fill="none" stroke="#fff" stroke-width="2"/><line x1="11" y1="11" x2="16" y2="16" stroke="#fff" stroke-width="2"/></svg>
</nav>
<div class="abs brand brand-center">RIDGELINE HAUL CARRIERS</div>
<div class="abs see-more">See More &#9655;</div>
<div class="abs hero-arrow" style="left:27px"><svg width="48" height="48" viewBox="0 0 48 48"><path d="M27 17l-7 7 7 7" fill="none" stroke="#e8202a" stroke-width="2.5"/></svg></div>
<div class="abs hero-arrow" style="left:1123px"><svg width="48" height="48" viewBox="0 0 48 48"><path d="M21 17l7 7-7 7" fill="none" stroke="#e8202a" stroke-width="2.5"/></svg></div>
<div class="abs trucks" role="img" aria-label="Three orange and yellow semi truck cabs side by side"></div>

<section>
  <svg class="abs about-ring" width="400" height="400" viewBox="0 0 400 400"><path d="M30 270 A188 188 0 1 1 250 384" fill="none" stroke="#e8202a" stroke-width="5"/></svg>
  <div class="abs about-photo" role="img" aria-label="Red semi truck driving on a highway"></div>
  <h2 class="abs heading about-title">About Us</h2>
  <p class="abs about-text">Lorem ipsum dolor sit amet, consectetur adipiscing elit, sed do eiusmod tempor incididunt ut labore et dolore magna aliqua. Ut enim ad minim veniam, quis nostrud exercitation ullamco laboris nisi ut aliquip ex ea commodo consequat. Duis aute irure dolor in reprehenderit in voluptate velit esse cillum dolore eu fugiat nulla pariatur. Excepteur sint occaecat cupidatat non proident, sunt in culpa qui officia deserunt mollit anim id est laborum.</p>
  <a class="abs btn btn-red learn-more">Learn More</a>
</section>

<section class="abs services"></section>
<h2 class="abs heading services-title">Our Services</h2>
<div class="abs svc-arrow" style="left:28px"><svg width="48" height="48" viewBox="0 0 48 48"><path d="M27 17l-7 7 7 7" fill="none" stroke="#fff" stroke-width="2.5"/></svg></div>
<div class="abs svc-arrow" style="left:1124px"><svg width="48" height="48" viewBox="0 0 48 48"><path d="M21 17l7 7-7 7" fill="none" stroke="#fff" stroke-width="2.5"/></svg></div>

<div class="abs svc-img" style="left:104px;background:linear-gradient(180deg,#3f86c9 0%,#bcd3e6 50%,#8a8f95 100%)" role="img" aria-label="Red truck on a road with snowy mountains"></div>
<h3 class="abs heading svc-name" style="left:106px">Transport</h3>
<p class="abs svc-text" style="left:106px">Lorem ipsum dolor sit amet adipisicing eiusmod tempor elementum ut labore et dolore magna aliqua ad minim veniam, nostrud quis exercitation.</p>
<a class="abs svc-more" style="left:110px">Read More</a>

<div class="abs svc-img" style="left:447px;background:linear-gradient(180deg,#f3c27a 0%,#c98a4a 55%,#6b4a2e 100%)" role="img" aria-label="Truck on an open road at sunset"></div>
<h3 class="abs heading svc-name" style="left:447px">Earthworks</h3>
<p class="abs svc-text" style="left:447px">Lorem ipsum dolor sit amet adipisicing eiusmod tempor elementum ut labore et dolore magna aliqua ad minim veniam, nostrud quis exercitation.</p>
<a class="abs svc-more" style="left:451px">Read More</a>

<div class="abs svc-img" style="left:789px;background:linear-gradient(180deg,#6f9fcf 0%,#c7d3dd 50%,#9da3a8 100%)" role="img" aria-label="Cooling towers of a power plant"></div>
<h3 class="abs heading svc-name" style="left:789px">Radioactive Materials</h3>
<p class="abs svc-text" style="left:789px">Lorem ipsum dolor sit amet adipisicing eiusmod tempor elementum ut labore et dolore magna aliqua ad minim veniam, nostrud quis exercitation.</p>
<a class="abs svc-more" style="left:793px">Read More</a>

<section class="abs pro-band" role="img" aria-label="Truck on a highway under a dark evening sky"></section>
<div class="abs pro-truck" role="img" aria-label="White semi truck with trailer"></div>
<div class="abs pro-kicker">Professional Services</div>
<h2 class="abs pro-title">We are an established business that has been around for over 15 years</h2>
<a class="abs btn btn-orange apply">Apply Now</a>

<div class="abs features"></div>
<div class="abs feat-icon" style="left:309px"><svg width="80" height="80" viewBox="0 0 80 80"><path d="M24 48a16 16 0 0 1 32 0z" fill="none" stroke="#fff" stroke-width="3"/><rect x="20" y="48" width="40" height="5" fill="#fff"/><line x1="40" y1="32" x2="40" y2="42" stroke="#fff" stroke-width="3"/></svg></div>
<div class="abs feat-icon" style="left:778px"><svg width="80" height="80" viewBox="0 0 80 80"><rect x="22" y="30" width="24" height="18" fill="none" stroke="#fff" stroke-width="3"/><path d="M46 36h8l5 6v6h-13z" fill="none" stroke="#fff" stroke-width="3"/><circle cx="30" cy="51" r="3" fill="#fff"/><circle cx="53" cy="51" r="3" fill="#fff"/><line x1="14" y1="36" x2="20" y2="36" stroke="#fff" stroke-width="2"/><line x1="12" y1="42" x2="20" y2="42" stroke="#fff" stroke-width="2"/></svg></div>
<h3 class="abs feat-title" style="left:119px">Safe &amp; Secure</h3>
<p class="abs feat-text" style="left:119px">Donec sed eros fermentum, cursus dui eget, bibendum nibh. Donec scelerisque sollicitudin magna, in viverra lacus placerat quis. Maecenas tincidunt nisl</p>
<h3 class="abs feat-title" style="left:597px">International Transport</h3>
<p class="abs feat-text" style="left:597px">Donec sed eros fermentum, cursus dui eget, bibendum nibh. Donec scelerisque sollicitudin magna, in viverra lacus placerat quis. Maecenas tincidunt nisl</p>

<h2 class="abs heading ded-title">We’re Dedicated to Customers &amp; Focused on Quality</h2>
<p class="abs ded-text">Sed ut perspiciatis unde omnis iste natus error sit voluptatem accusantium doloremque laudantium, totam rem aperiam, eaque ipsa quae ab illo inventore veritatis et quasi architecto</p>
<a class="abs btn btn-red quote">Request a Free Quote</a>

<footer class="abs footer"></footer>
<div class="abs brand brand-foot" style="font-size:30px;top:3100px">RIDGELINE HAUL</div>
<div class="abs social" style="left:171px"></div>
<div class="abs social" style="left:215px"></div>
<div class="abs social" style="left:262px"></div>

<h4 class="abs foot-head" style="left:453px">Quick Links</h4>
<ul class="abs foot-list" style="left:453px"><li>Home</li><li>About</li><li>Services</li><li>Jobs</li><li>Contact</li></ul>
<h4 class="abs foot-head" style="left:631px">Services</h4>
<ul class="abs foot-list" style="left:631px"><li>Transport</li><li>Earthworks</li><li>Radioactive Materials</li></ul>
<h4 class="abs foot-head" style="left:858px">Contact Us</h4>
<div class="abs contact-row" style="top:3090px;width:280px"><b>Address:</b>#10,Sed ut perspiciatis unde omnis iste Washington</div>
<div class="abs contact-row" style="top:3157px"><b>Phone:</b>+1 555 014 2270</div>
<div class="abs contact-row" style="top:3196px"><b>Email:</b>jobs@ridgelinehaul.com</div>
<div class="abs copy">© 2019 Copyrights | All Rights Reserved</div>

</body>
</html>
```